Brightmill Data Works

Our company is about IT hardwares and IT solutions. IT hardware such as PC, RAMS, storage and servers. IT solutions such as project management, BA. We are also selling new technology too.

Target Market(s)

Consumer, Small to Medium Business, Corporate

Requirements
Must have
• The business card must have the following:
• Name:
• Title:
• Contact Number:
• Email address:
• Website:
• Color: Must match the logo color upgrade

```html
<!DOCTYPE html>
<html lang="en">
<head>
<meta charset="UTF-8">
<title>Brightmill Data Works – Business Card</title>
<link href="https://fonts.googleapis.com/css2?family=Archivo:wght@400;700;800&display=swap" rel="stylesheet">
<style>
  :root {
    --bg: #2b2b2d;
    --orange-light: #e09a40;
    --orange: #d17a2e;
    --orange-deep: #c5682a;
    --ink: #3c3c3e;
    --strip: #4a4a4c;
    --white: #ffffff;
  }
  * { box-sizing: border-box; margin: 0; padding: 0; }
  html, body {
    width: 1200px; height: 880px; overflow: hidden;
    background: var(--bg);
    font-family: "Archivo", Arial, sans-serif;
  }
  .canvas {
    position: relative; width: 1200px; height: 880px;
  }
  .card {
    position: absolute; left: 250px; width: 700px; height: 400px;
    border-radius: 26px; overflow: hidden;
    box-shadow: 0 10px 30px rgba(0,0,0,.45);
  }
  .card-front {
    top: 20px;
    background: linear-gradient(160deg, var(--orange-light) 0%, var(--orange) 55%, var(--orange-deep) 100%);
    display: flex; align-items: center; justify-content: center;
  }
  .brand {
    display: flex; align-items: center; gap: 14px;
    font-weight: 800; text-transform: uppercase; letter-spacing: 1px;
  }
  .brand-dot {
    width: 22px; height: 22px; border-radius: 50%;
  }
  .card-front .brand { color: var(--white); font-size: 40px; }
  .card-front .brand-dot { background: var(--white); }

  .card-back {
    top: 460px; background: var(--white);
  }
  .card-back .brand {
    position: absolute; left: 40px; top: 150px;
    color: var(--ink); font-size: 27px; width: 300px; flex-wrap: nowrap;
  }
  .card-back .brand-dot { background: var(--orange); flex: none; }
  .brand-name { line-height: 1.1; }
  .divider {
    position: absolute; left: 372px; top: 100px; width: 2px; height: 130px;
    background: linear-gradient(to bottom, rgba(209,122,46,0), var(--orange) 30%, var(--orange) 70%, rgba(209,122,46,0));
  }
  .contact {
    position: absolute; left: 400px; top: 96px;
  }
  .person-name {
    font-weight: 700; font-size: 22px; color: var(--ink); letter-spacing: .3px;
  }
  .person-title {
    font-size: 18px; color: var(--orange); margin-bottom: 14px;
  }
  .contact-list { list-style: none; }
  .contact-list li {
    display: flex; align-items: center; gap: 10px;
    font-size: 17px; color: var(--ink); line-height: 1.55;
  }
  .contact-list svg { width: 16px; height: 16px; flex: none; }
  .band {
    position: absolute; left: 0; right: 0; bottom: 0; height: 96px;
    background: linear-gradient(to bottom, var(--orange-light), var(--orange-deep));
    border-top: 8px solid var(--strip);
    display: flex; align-items: center; justify-content: center;
  }
  .address {
    color: var(--white); font-size: 18px; letter-spacing: .3px;
  }
</style>
</head>
<body>
<div class="canvas">
  <section class="card card-front">
    <div class="brand">
      <span class="brand-dot"></span>
      <span class="brand-name">Brightmill Data Works</span>
    </div>
  </section>

  <section class="card card-back">
    <div class="brand">
      <span class="brand-dot"></span>
      <span class="brand-name">Brightmill<br>Data Works</span>
    </div>
    <div class="divider"></div>
    <div class="contact">
      <p class="person-name">DANA WHITLOCK</p>
      <p class="person-title">Manager</p>
      <ul class="contact-list">
        <li>
          <svg viewBox="0 0 16 16" aria-hidden="true"><path fill="#d17a2e" d="M3 2h3l1 3-2 1.2a8 8 0 0 0 4.8 4.8L11 9l3 1v3a1 1 0 0 1-1 1A11 11 0 0 1 2 3a1 1 0 0 1 1-1z"/></svg>
          555-014-2290
        </li>
        <li>
          <svg viewBox="0 0 16 16" aria-hidden="true"><rect x="1" y="3" width="14" height="10" rx="1" fill="#d17a2e"/><path d="M1.5 3.5 8 9l6.5-5.5" stroke="#fff" stroke-width="1.3" fill="none"/></svg>
          hello@brightmilldata.com
        </li>
        <li>
          <svg viewBox="0 0 16 16" aria-hidden="true"><circle cx="8" cy="8" r="6.5" fill="none" stroke="#d17a2e" stroke-width="1.4"/><ellipse cx="8" cy="8" rx="2.8" ry="6.5" fill="none" stroke="#d17a2e" stroke-width="1.2"/><path d="M1.5 8h13" stroke="#d17a2e" stroke-width="1.2"/></svg>
          www.brightmilldata.com
        </li>
      </ul>
    </div>
    <div class="band">
      <p class="address">PO BOX 48 Harlow Lane, 7th street Ballarat</p>
    </div>
  </section>
</div>
</body>
</html>
```